Pellmore's Pick magazine ad

This is a full page ad in a magazine announcing that I won The Pick Of Pellmore Valley Realtor for 2023. The dimensions for the full page ad are 7.125" x 9.75"
I would like it to say "Thank You Harford County for voting me Pellmore's Pick Realtor for 2022 & 2023!"

I am honored that the residents of this county have recognized my integrity, values, willingness to go above and beyond, to save my clients tons of money and stress, and to constantly pour back into this community.

If you are ever thinking about buying or selling a house, please don't hesitate to reach out, I am available 24/7 by text or phone call to save you money and provide the best top notch service:

Corwin Ashlund
call/text 410-555-0172

Small at the bottom:
www.MarlowCrestHomes.com
2749 W Amberly Ln, Bel Air, MD 21014
833-555-0149

I am attaching my logo, the Pellmore's Pick 2023 logo, my picture, and last years ad (I'm hoping to make this years ad different and better)

```html
<!DOCTYPE html>
<html lang="en">
<head>
<meta charset="UTF-8">
<title>Pellmore's Pick Realtor – Thank You</title>
<link href="https://fonts.googleapis.com/css2?family=Great+Vibes&family=Prata&family=Lexend:wght@300;400;600;700&display=swap" rel="stylesheet">
<style>
  :root {
    --navy: #14305a;
    --ink: #1f3050;
    --charcoal: #333333;
    --band-blue: #3a7fb3;
    --band-deep: #2a6ea8;
    --script-red: #ff3b12;
    --accent-red: #ff3b12;
    --panel-grey: #e8e8ea;
    --sky: #e3ebf4;
    --white: #ffffff;
    --badge-dark: #231f20;
  }
  * { margin: 0; padding: 0; box-sizing: border-box; }
  html, body { width: 842px; height: 1200px; overflow: hidden; background: var(--white); }
  .ad {
    position: relative;
    width: 842px;
    height: 1200px;
    overflow: hidden;
    background: var(--white);
    font-family: "Lexend", sans-serif;
  }
  .backdrop { position: absolute; inset: 0; }

  .team-mark {
    position: absolute;
    left: 82px;
    top: 140px;
    width: 300px;
    text-align: center;
    font-family: "Prata", serif;
    color: var(--navy);
  }
  .team-mark .dot {
    width: 80px; height: 80px;
    border-radius: 50%;
    background: var(--navy);
    margin: 0 auto 34px;
  }
  .team-mark .name { font-size: 27px; line-height: 1; white-space: nowrap; }
  .team-mark .sub { font-size: 10.5px; letter-spacing: 2.4px; margin-top: 12px; text-transform: uppercase; white-space: nowrap; }

  .portrait {
    position: absolute;
    left: 440px; top: 123px;
    width: 348px; height: 940px;
    border-radius: 150px 150px 20px 20px;
    background: linear-gradient(180deg, rgba(44,62,96,0.55) 0%, rgba(120,140,170,0.35) 45%, rgba(200,200,200,0.35) 70%, rgba(220,220,222,0.25) 100%);
  }

  .award-seal { position: absolute; left: 78px; top: 494px; width: 210px; height: 182px; }

  .thanks {
    position: absolute;
    left: 445px; top: 408px;
    font-family: "Great Vibes", cursive;
    font-size: 80px;
    color: var(--script-red);
    line-height: 1;
    white-space: nowrap;
  }
  .county {
    position: absolute;
    left: 354px; top: 502px;
    font-family: "Prata", serif;
    font-size: 42px;
    line-height: 1.1;
    color: var(--white);
    white-space: nowrap;
  }
  .voting {
    position: absolute;
    left: 355px; top: 562px;
    font-size: 22px;
    color: var(--white);
    white-space: nowrap;
    letter-spacing: -0.3px;
  }
  .voting .hl { color: var(--accent-red); font-weight: 600; }
  .rule { position: absolute; left: 355px; top: 594px; width: 487px; height: 1px; background: rgba(255,255,255,0.8); }
  .years {
    position: absolute;
    left: 355px; top: 600px;
    width: 487px;
    text-align: center;
    font-size: 52px;
    font-weight: 700;
    color: var(--white);
    letter-spacing: -1px;
  }

  .message {
    position: absolute;
    left: 75px; top: 784px;
    width: 722px;
    font-size: 20px;
    font-weight: 300;
    line-height: 30.5px;
    color: var(--ink);
    letter-spacing: -0.4px;
  }
  .message p + p { margin-top: 14px; }

  .agent-name {
    position: absolute;
    left: 75px; top: 1024px;
    font-size: 28px;
    font-weight: 600;
    color: var(--charcoal);
    letter-spacing: -0.5px;
  }
  .agent-phone {
    position: absolute;
    left: 75px; top: 1073px;
    font-size: 31px;
    font-weight: 300;
    color: var(--ink);
  }

  .office-info {
    position: absolute;
    right: 23px; top: 1069px;
    text-align: right;
    font-size: 14.5px;
    font-weight: 300;
    line-height: 25.5px;
    color: var(--white);
  }
</style>
</head>
<body>
<div class="ad">
  <svg class="backdrop" width="842" height="1200" viewBox="0 0 842 1200" aria-hidden="true">
    <defs>
      <linearGradient id="skyFade" x1="0" y1="0" x2="1" y2="0">
        <stop offset="0" stop-color="#ffffff"/>
        <stop offset="1" stop-color="#e0e9f3"/>
      </linearGradient>
      <linearGradient id="bandFade" x1="0" y1="0" x2="1" y2="0">
        <stop offset="0" stop-color="#ffffff" stop-opacity="0.2"/>
        <stop offset="0.35" stop-color="#bcd0e3"/>
        <stop offset="0.7" stop-color="#5c93c2"/>
        <stop offset="1" stop-color="#3a7fb3"/>
      </linearGradient>
      <linearGradient id="edgeFade" x1="0" y1="0" x2="1" y2="0">
        <stop offset="0" stop-color="#2a6ea8" stop-opacity="0"/>
        <stop offset="1" stop-color="#2a6ea8"/>
      </linearGradient>
      <linearGradient id="footFade" x1="0" y1="0" x2="1" y2="0">
        <stop offset="0" stop-color="#e3ebf4"/>
        <stop offset="1" stop-color="#3a7fb3"/>
      </linearGradient>
    </defs>
    <rect x="73" y="101" width="743" height="720" fill="url(#skyFade)"/>
    <polygon points="21,766 842,680 842,1160 21,1160" fill="var(--panel-grey)"/>
  </svg>

  <div class="portrait" role="img" aria-label="Portrait photo of the realtor standing in a navy blazer and light trousers"></div>

  <svg class="backdrop" width="842" height="1200" viewBox="0 0 842 1200" aria-hidden="true">
    <polygon points="45,452 842,365 842,668 20,766" fill="url(#bandFade)" opacity="0.92"/>
    <polygon points="20,766 842,668 842,680 20,772" fill="url(#edgeFade)"/>
    <polygon points="530,1063 842,1063 842,1149 441,1149" fill="var(--band-blue)"/>
    <rect x="21" y="1157" width="821" height="7" fill="#dde6ef"/>
    <rect x="21" y="1170" width="821" height="30" fill="url(#footFade)"/>
  </svg>

  <div class="team-mark">
    <div class="dot"></div>
    <div class="name">MARLOW CREST TEAM</div>
    <div class="sub">at Brightwell Realty</div>
  </div>

  <svg class="award-seal" viewBox="0 0 210 182" role="img" aria-label="Pellmore's Pick 2023 winner seal">
    <polygon points="105,2 170,18 206,70 200,130 160,172 100,180 40,168 6,125 4,65 40,18" fill="var(--badge-dark)" transform="rotate(-8 105 91)"/>
  </svg>

  <div class="thanks">Thank You</div>
  <div class="county">HARFORD COUNTY</div>
  <div class="voting">for voting me <span class="hl">PELLMORE'S</span> Pick Realtor for</div>
  <div class="rule"></div>
  <div class="years">2022 &amp; 2023!</div>

  <div class="message">
    <p>I am honored that the residents of this county have recognized my integrity, values, willingness to go above and beyond, to save my clients tons of money and stress, and to constantly pour back into this community.</p>
    <p>If you are ever thinking about buying or selling a house, please don't hesitate to reach out, I am available 24/7 by text or phone call to save you money and provide the best top notch service:</p>
  </div>

  <div class="agent-name">Corwin Ashlund</div>
  <div class="agent-phone">Call/Text: 410-555-0172</div>

  <div class="office-info">
    www.MarlowCrestHomes.com<br>
    2749 W Amberly Ln, Bel Air, MD 21014<br>
    833-555-0149
  </div>
</div>
</body>
</html>
```